Business Cards for a law firm

Business cards for our law firm. Use our silhoette logo and OAK PARTNERS - check our website (www.oakpartners.example)

Contact Information for Business Card

our silhouette logo, OAK PARTNERS, 800-555-0147, Dorian Pemberton, dorian@oakpartners.example

Requirements
Must have
• our silhouette logo, OAK PARTNERS, 800-555-0147, Dorian Pemberton, dorian@oakpartners.example

```html
<!DOCTYPE html>
<html lang="en">
<head>
<meta charset="utf-8">
<title>Oak Partners – Business Cards</title>
<link rel="stylesheet" href="https://fonts.googleapis.com/css2?family=Marcellus+SC&family=Arimo:wght@400&display=swap">
<style>
  :root {
    --stage: #3d3d3d;
    --navy: #1b3068;
    --navy-deep: #15275a;
    --white: #ffffff;
    --mist: #c9d2e6;
    --sky: #4f9be8;
    --card-radius: 24px;
  }
  * { box-sizing: border-box; margin: 0; padding: 0; }
  html, body {
    width: 1200px; height: 803px; overflow: hidden;
    background: var(--stage);
  }
  .stage {
    position: relative; width: 1200px; height: 803px;
  }
  .card {
    position: absolute; top: 252px;
    width: 520px; height: 300px;
    border-radius: var(--card-radius);
    background: var(--navy);
    overflow: hidden;
  }
  .card--front { left: 40px; }
  .card--back { left: 640px; }

  .front__portrait {
    position: absolute; top: 0; right: 0;
    width: 200px; height: 300px;
    background: linear-gradient(160deg, var(--white) 0%, var(--white) 40%, var(--mist) 100%);
  }
  .front__notch {
    position: absolute; left: -14px; top: 218px;
    width: 28px; height: 28px; border-radius: 50%;
    background: var(--white);
  }
  .front__firm {
    position: absolute; left: 40px; top: 78px;
    font-family: "Marcellus SC", serif;
    font-size: 32px; letter-spacing: 3px;
    color: var(--white);
  }
  .front__name {
    position: absolute; left: 40px; top: 160px;
    font-family: "Marcellus SC", serif;
    font-size: 20px; letter-spacing: 1.5px;
    color: var(--white);
  }
  .front__contacts {
    position: absolute; left: 40px; top: 200px;
    list-style: none;
    font-family: "Arimo", sans-serif;
    font-size: 13px; line-height: 20px;
    color: var(--white);
  }
  .front__contacts li { display: flex; align-items: center; gap: 8px; }
  .front__contacts svg { width: 11px; height: 11px; flex: none; }

  .back__brand {
    position: absolute; left: 70px; top: 132px;
    display: flex; align-items: center; gap: 16px;
  }
  .back__dot {
    width: 30px; height: 30px; border-radius: 50%;
    background: var(--navy-deep);
  }
  .back__name {
    font-family: "Marcellus SC", serif;
    font-size: 34px; letter-spacing: 5px;
    color: var(--sky);
  }
</style>
</head>
<body>
<main class="stage">
  <section class="card card--front">
    <div class="front__portrait" role="img" aria-label="Portrait area showing the two partners standing side by side"></div>
    <div class="front__notch"></div>
    <h1 class="front__firm">Oak Partners</h1>
    <h2 class="front__name">Dorian Pemberton</h2>
    <ul class="front__contacts">
      <li>
        <svg viewBox="0 0 12 12" aria-hidden="true"><path d="M2.5 1 L4.5 1 L5 3.5 L3.8 4.5 Q5 7 7.5 8.2 L8.5 7 L11 7.5 L11 9.5 Q10.5 11 9 11 Q1 10 1 3 Q1 1.5 2.5 1Z" fill="#fff"/></svg>
        800-555-0147
      </li>
      <li>
        <svg viewBox="0 0 12 12" aria-hidden="true"><rect x="1" y="2.5" width="10" height="7" fill="#fff"/><path d="M1 2.5 L6 6.5 L11 2.5" stroke="#1b3068" stroke-width="1.2" fill="none"/></svg>
        dorian@oakpartners.example
      </li>
      <li>
        <svg viewBox="0 0 12 12" aria-hidden="true"><circle cx="6" cy="6" r="5" fill="#fff"/><path d="M1 6 H11 M6 1 Q3 6 6 11 M6 1 Q9 6 6 11" stroke="#1b3068" stroke-width="0.9" fill="none"/></svg>
        www.oakpartners.example
      </li>
    </ul>
  </section>

  <section class="card card--back">
    <div class="back__brand">
      <span class="back__dot"></span>
      <span class="back__name">Oak Partners</span>
    </div>
  </section>
</main>
</body>
</html>
```